Lantern Hollow Brewing Company New Website with Food Ordering

We need a wordpress-based website for a local brewery & pizza kitchen. The final design will have 6 primary pages: home page, order pizza, our beers, visit us, about us, merch store. The website must integrate with tillpoint for kitchens for online ordering for takeout and delivery. It will also a feature a selection of beers and help customers navigate to the brewery and find hours of operation. The existing website is lanternhollowbrew.example. This is a very old website.

Industry/Entity Type

Brewery and food service

Coding

Coded - Design and coding required

Number of Pages Required

5+ page

Font styles to use
Sans Serif

Requirements
Must have
• ability to integrate seamlessly with tillpoint for kitchens, 21+ age gate
Nice to have
• see attached pdf

```html
<!DOCTYPE html>
<html lang="en">
<head>
<meta charset="utf-8">
<title>Lantern Hollow Brewing Company</title>
<link href="https://fonts.googleapis.com/css2?family=Libre+Baskerville:wght@700&family=Roboto+Condensed:wght@400;700&display=swap" rel="stylesheet">
<style>
:root{
  --red:#c8102e;
  --dark:#231f20;
  --ink:#2b2627;
  --grey:#6f6a6b;
  --white:#ffffff;
  --sans:"Roboto Condensed",sans-serif;
  --serif:"Libre Baskerville",serif;
}
*{margin:0;padding:0;box-sizing:border-box}
html,body{width:1200px;height:2457px;overflow:hidden}
body{position:relative;background:var(--white);font-family:var(--sans);color:var(--ink)}
.abs{position:absolute}

/* header */
.topline{left:0;top:0;width:1200px;height:5px;background:var(--dark)}
.brand{left:112px;top:36px;display:flex;align-items:center;gap:10px;font:700 26px/1 var(--sans);color:var(--red);text-transform:uppercase}
.brand-square{width:38px;height:38px;background:var(--red)}
.contact-pill{left:529px;top:0;width:557px;height:46px;background:var(--dark);border-radius:0 0 40px 40px;display:flex;align-items:center;justify-content:space-around;color:var(--white);font-size:14px}
.contact-pill span{display:flex;align-items:center;gap:14px}
.dot{width:34px;height:34px;border-radius:50%;background:var(--white);display:flex;align-items:center;justify-content:center}
.main-nav{left:437px;top:76px;display:flex;gap:36px;font:700 15px/1 var(--sans);color:var(--dark)}
.badge{left:940px;top:52px;width:152px;height:66px}
.badge-label{left:940px;top:78px;width:152px;text-align:center;color:var(--white);font:700 13px/1 var(--sans);text-transform:uppercase}

/* hero */
.hero{left:0;top:124px;width:1200px;height:600px;clip-path:polygon(0 0,100% 0,100% 80%,50% 100%,0 80%);
  background:radial-gradient(ellipse 55% 45% at 50% 40%,#b9773a 0%,#8a3a22 45%,#2a1d1a 80%,#141111 100%)}
.hero-title{left:0;top:366px;width:1200px;text-align:center;color:var(--white);font:700 37px/49px var(--serif);text-shadow:0 2px 6px rgba(0,0,0,.5)}

/* feature tiles */
.tile{width:232px;height:231px;display:flex;flex-direction:column;align-items:center;justify-content:flex-end;padding-bottom:48px;color:var(--white);font:700 20px/1 var(--sans);text-transform:uppercase}
.tile svg{margin-bottom:26px}
.tile-dark{background:var(--dark)}
.tile-red{background:var(--red)}
.slant-down{clip-path:polygon(0 0,100% 22%,100% 100%,0 100%)}
.slant-up{clip-path:polygon(0 22%,100% 0,100% 100%,0 100%)}
.hexbtn{width:46px;height:52px;display:flex;align-items:center;justify-content:center;clip-path:polygon(50% 0,100% 25%,100% 75%,50% 100%,0 75%,0 25%);color:var(--white);font:700 26px/1 var(--sans)}
.hex-red{background:var(--red)}
.hex-dark{background:var(--dark)}

/* intro */
.section-title{left:0;width:1200px;text-align:center;font:700 33px/1 var(--serif);text-transform:uppercase}
.divider{left:510px;width:180px;height:24px}
.copy{left:126px;width:948px;text-align:center;font-size:14px;line-height:26px}
.copy-grey{color:var(--grey)}
.hexphoto{width:232px;height:266px;background:#f0f0f0;clip-path:polygon(50% 0,100% 25%,100% 75%,50% 100%,0 75%,0 25%);filter:drop-shadow(0 0 4px rgba(0,0,0,.2))}
.hexphoto i{position:absolute;inset:7px;clip-path:polygon(50% 0,100% 25%,100% 75%,50% 100%,0 75%,0 25%);
  background:radial-gradient(ellipse 34% 30% at 50% 50%,#d9682c 0%,#c23a22 55%,#2a2a2c 75%,#1c1c1e 100%)}
.btn{top:1520px;width:168px;height:50px;border-radius:4px;display:flex;align-items:center;justify-content:center;color:var(--white);font:700 16px/1 var(--sans);text-transform:uppercase}

/* call band */
.callband{left:0;top:1677px;width:1200px;height:780px;background:radial-gradient(ellipse 70% 60% at 50% 40%,#d4213c 0%,#b3162c 60%,#8e1022 100%)}
.callbtn{left:499px;top:1938px;width:202px;height:51px;background:var(--dark);border-radius:4px;display:flex;align-items:center;gap:18px;padding-left:6px;color:var(--white);font:700 16px/1 var(--sans)}
.callicon{width:38px;height:38px;background:var(--white);border-radius:4px;display:flex;align-items:center;justify-content:center}

/* footer */
.footer-shape{left:0;top:2030px;width:1200px;height:427px}
.footer-brand{left:0;top:2170px;width:1200px;text-align:center;font:700 34px/1 var(--sans);color:var(--white);text-transform:uppercase}
.footer-nav{left:0;top:2275px;width:1200px;display:flex;justify-content:center;gap:43px;font:700 18px/1 var(--sans);color:var(--white);text-transform:uppercase}
.footer-contact{left:0;top:2316px;width:1200px;display:flex;justify-content:center;align-items:center;gap:16px;color:var(--white);font-size:16px}
.social{left:0;top:2352px;width:1200px;display:flex;justify-content:center;gap:7px}
.social span{width:34px;height:34px;border-radius:50%;border:2px solid var(--white)}
.social span.on{background:var(--red);border-color:var(--red)}
.rule{left:112px;top:2406px;width:976px;height:1px;background:#4a4445}
.copyright{left:0;top:2424px;width:1200px;text-align:center;color:var(--white);font-size:13px}
</style>
</head>
<body>

<!-- header -->
<div class="abs topline"></div>
<div class="abs brand"><span class="brand-square"></span>Lantern Hollow</div>
<div class="abs contact-pill">
  <span><i class="dot"><svg width="14" height="14" viewBox="0 0 24 24"><path fill="#c8102e" d="M6.6 10.8a15 15 0 0 0 6.6 6.6l2.2-2.2a1 1 0 0 1 1-.25 11.4 11.4 0 0 0 3.6.57 1 1 0 0 1 1 1V20a1 1 0 0 1-1 1A17 17 0 0 1 3 4a1 1 0 0 1 1-1h3.5a1 1 0 0 1 1 1c0 1.25.2 2.45.57 3.57a1 1 0 0 1-.25 1z"/></svg></i>+1 207-555-0142</span>
  <span><i class="dot"><svg width="14" height="12" viewBox="0 0 24 18"><path fill="#c8102e" d="M0 0h24v18H0z"/><path fill="none" stroke="#fff" stroke-width="2" d="M1 1l11 8 11-8"/></svg></i>hello@lanternhollowbrew.example</span>
</div>
<nav class="abs main-nav"><span>THE KITCHEN</span><span>OUR BEERS</span><span>VISIT US</span><span>ABOUT US</span><span>MERCH</span></nav>
<svg class="abs badge" viewBox="0 0 152 66"><polygon fill="#c8102e" points="0,33 30,24 24,8 52,16 62,0 78,12 96,2 104,16 130,10 124,26 152,33 124,40 132,56 104,50 96,66 78,54 60,64 52,50 24,58 32,42"/><polygon fill="#231f20" points="10,33 36,27 32,14 56,21 64,8 78,18 94,10 100,22 122,17 118,29 140,33 118,37 124,50 100,45 94,56 78,48 62,56 56,45 32,52 38,39"/></svg>
<div class="abs badge-label">Try Ember!</div>

<!-- hero -->
<div class="abs hero" role="img" aria-label="Photo of a square Detroit-style pizza with tomatoes, basil and pepperoni in a dark pan"></div>
<h1 class="abs hero-title">SQUARE PIZZA AND GREAT BEER<br>IN PORTLAND, MAINE</h1>

<!-- tiles -->
<div class="abs tile tile-dark slant-down" style="left:112px;top:561px">
  <svg width="78" height="68" viewBox="0 0 78 68" fill="none" stroke="#fff" stroke-width="2.5"><rect x="2" y="2" width="74" height="48" rx="3"/><path d="M2 42h74M30 50l-4 14h26l-4-14M20 64h38"/><path d="M10 10h22M10 18h22M10 26h16"/><path d="M48 36l10-24 10 24z"/></svg>
  Order Pizza
</div>
<div class="abs hexbtn hex-red" style="left:204px;top:767px">+</div>

<div class="abs tile tile-red slant-down" style="left:360px;top:618px">
  <svg width="66" height="70" viewBox="0 0 66 70" fill="none" stroke="#fff" stroke-width="2.5"><rect x="2" y="2" width="44" height="66"/><path d="M10 12h8v8h-8zM24 12h8v8h-8zM10 28h8v8h-8zM24 28h8v8h-8zM16 68V52h16v16"/><path d="M52 66c-8-10-10-14-10-18a10 10 0 0 1 20 0c0 4-2 8-10 18z"/><circle cx="52" cy="48" r="3"/></svg>
  Visit Us
</div>
<div class="abs hexbtn hex-dark" style="left:453px;top:824px">+</div>

<div class="abs tile tile-dark slant-up" style="left:609px;top:618px">
  <svg width="70" height="70" viewBox="0 0 70 70" fill="none" stroke="#fff" stroke-width="2.5"><rect x="2" y="36" width="66" height="32"/><path d="M2 50h66"/><rect x="8" y="14" width="14" height="22"/><rect x="28" y="6" width="14" height="30"/><rect x="48" y="14" width="14" height="22"/><path d="M16 62a8 8 0 0 1 16 0M38 62a8 8 0 0 1 16 0"/></svg>
  Our Beers
</div>
<div class="abs hexbtn hex-red" style="left:701px;top:824px">+</div>

<div class="abs tile tile-red slant-up" style="left:857px;top:561px">
  <svg width="64" height="70" viewBox="0 0 64 70" fill="none" stroke="#fff" stroke-width="2.5"><path d="M8 6h34v62H2V12z"/><path d="M10 24h24M10 34h24M10 44h24M10 54h18"/><circle cx="50" cy="14" r="11"/><path d="M50 10v10M50 6v1"/></svg>
  About Us
</div>
<div class="abs hexbtn hex-dark" style="left:950px;top:767px">+</div>

<!-- intro -->
<h2 class="abs section-title" style="top:977px">What is Detroit-style pizza?</h2>
<svg class="abs divider" style="top:1023px" viewBox="0 0 180 24"><path d="M0 12h74M106 12h74" stroke="#231f20" stroke-width="2"/><rect x="76" y="1" width="28" height="22" fill="#fff" stroke="#c8102e" stroke-width="3"/></svg>
<p class="abs copy copy-grey" style="top:1071px">Sed ut perspiciatis unde omnis iste natus error sit voluptatem accusantium doloremque laudantium, totam rem aperiam, eaque ipsa quae ab illo inventore veritatis et quasi architecto beatae vitae dicta sunt explicabo. Nemo enim ipsam voluptatem quia voluptas sit aspernatur aut odit aut fugit, sed quia consequuntur magni dolores eos qui ratione voluptatem sequi nesciunt. Neque porro quisquam est, qui dolorem ipsum quia dolor sit amet, consectetur, adipisci velit, sed quia non numquam eius modi tempora incidunt ut labore et dolore magnam aliquam quaerat voluptatem.</p>

<div class="abs hexphoto" style="left:112px;top:1205px" role="img" aria-label="Photo of a pizza with peppers on a dark stone surface"><i></i></div>
<div class="abs hexphoto" style="left:366px;top:1205px" role="img" aria-label="Photo of a margherita pizza with basil on a dark stone surface"><i></i></div>
<div class="abs hexphoto" style="left:610px;top:1205px" role="img" aria-label="Photo of a pizza with olives and tomatoes on a dark stone surface"><i></i></div>
<div class="abs hexphoto" style="left:858px;top:1205px" role="img" aria-label="Photo of a pizza with mushrooms and ham on a dark stone surface"><i></i></div>

<div class="abs btn" style="left:427px;background:var(--red)">Order Online</div>
<div class="abs btn" style="left:604px;background:var(--dark)">View Full Menu</div>

<!-- call band -->
<div class="abs callband" role="img" aria-label="Red-tinted close-up photo of pepperoni pizza"></div>
<h2 class="abs section-title" style="top:1745px;color:var(--white)">Questions? Give us a call</h2>
<svg class="abs divider" style="top:1788px" viewBox="0 0 180 24"><path d="M0 12h74M106 12h74" stroke="#fff" stroke-width="2"/><rect x="76" y="1" width="28" height="22" fill="none" stroke="#fff" stroke-width="3"/></svg>
<p class="abs copy" style="top:1833px;color:var(--white)">Sed ut perspiciatis unde omnis iste natus error sit voluptatem accusantium doloremque laudantium, totam rem aperiam, eaque ipsa quae ab illo inventore veritatis et quasi architecto beatae vitae dicta sunt explicabo. Nemo enim ipsam voluptatem quia voluptas sit aspernatur aut odit aut fugit, sed quia consequuntur magni dolores eos qui ratione voluptatem sequi nesciunt neque po i dolorem ipsum quia.</p>
<div class="abs callbtn"><span class="callicon"><svg width="18" height="18" viewBox="0 0 24 24"><path fill="#c8102e" d="M6.6 10.8a15 15 0 0 0 6.6 6.6l2.2-2.2a1 1 0 0 1 1-.25 11.4 11.4 0 0 0 3.6.57 1 1 0 0 1 1 1V20a1 1 0 0 1-1 1A17 17 0 0 1 3 4a1 1 0 0 1 1-1h3.5a1 1 0 0 1 1 1c0 1.25.2 2.45.57 3.57a1 1 0 0 1-.25 1z"/></svg></span>+1 207-555-0142</div>

<!-- footer -->
<svg class="abs footer-shape" viewBox="0 0 1200 427">
  <polygon fill="#fff" points="200,134 598,12 1000,134 598,50"/>
  <polygon fill="#c8102e" points="200,134 598,50 1000,134 598,64"/>
  <polygon fill="#231f20" points="0,183 598,64 1200,183 1200,427 0,427"/>
</svg>
<div class="abs footer-brand">Lantern Hollow</div>
<nav class="abs footer-nav"><span>Home</span><span>The Kitchen</span><span>Our Beers</span><span>Visit Us</span><span>About Us</span><span>Merch</span></nav>
<div class="abs footer-contact">
  <svg width="14" height="14" viewBox="0 0 24 24"><path fill="#c8102e" d="M6.6 10.8a15 15 0 0 0 6.6 6.6l2.2-2.2a1 1 0 0 1 1-.25 11.4 11.4 0 0 0 3.6.57 1 1 0 0 1 1 1V20a1 1 0 0 1-1 1A17 17 0 0 1 3 4a1 1 0 0 1 1-1h3.5a1 1 0 0 1 1 1c0 1.25.2 2.45.57 3.57a1 1 0 0 1-.25 1z"/></svg>
  <span>+1 207-555-0142</span><span>|</span>
  <svg width="16" height="12" viewBox="0 0 24 18"><path fill="#c8102e" d="M0 0h24v18H0z"/><path fill="none" stroke="#231f20" stroke-width="2" d="M1 1l11 8 11-8"/></svg>
  <span>hello@lanternhollowbrew.example</span>
</div>
<div class="abs social"><span class="on"></span><span></span><span></span></div>
<div class="abs rule"></div>
<div class="abs copyright">© 2022 LANTERN HOLLOW BREWING &nbsp;|&nbsp; All Rights Reserved</div>

</body>
</html>
```